interior designer/stylist looking for a letter press business card to reflect the stylish work

Hello Designers,
I need a business card design for an company called Mosaic Interior Design. I'm aiming at the high end residential and private client market in London providing sleek simple interiors. I'd like my business card to be pinterest worthy and expensive looking, i want people to pin it and for it to have a sought after look, and want prospective customers to hire me as their interior designer as my card is so beautiful.
I love letter press design. I also like the use of colour/foil on the edge.
Colour combos & general things I like -
Black and White
Navy Blue and Gold
Neutral colours (muted palette of greys whites navys beiges)
White Marble & brass
Vorelle (fashion designer)
....also open to other suggestions....
Please dont take the pink in the attached photos too literally. i'd like the card to look more masculine than feminine.
I'd like Mosaic on one side in one font, with interior design underneath so one word will make the statement....... unless anyone has any other ideas, open to suggestions.
I'd like a really simple font and for the whole card to look very graphic.
my details -
Petra Wendlecombe
Interior Designer & Stylist
email petra@mosaicinteriordesign.co.uk
phone +447311584209
website wwww.mosaicinteriordesign.co.uk
GO GO GO!! EXCITED TO SEE THE OUTCOME!!
x P
Target Market(s)
High End Residential and private clients
Industry/Entity Type
Business
Contact Information for Business Card
Mosaic Interior Design & Styling
Petra Wendlecombe
phone +447311584209

```html
<!DOCTYPE html>
<html lang="en">
<head>
<meta charset="utf-8">
<title>Mosaic Interior Design — Business Card</title>
<link rel="stylesheet" href="https://fonts.googleapis.com/css2?family=Source+Sans+3:wght@400;600&display=swap">
<style>
  :root {
    --stage-top: #2b2b2b;
    --stage-bottom: #040404;
    --card-amber: #f9a81b;
    --ink: #1f1d1a;
  }
  * { margin: 0; padding: 0; box-sizing: border-box; }
  html, body { width: 1200px; height: 900px; overflow: hidden; }
  body {
    position: relative;
    background: linear-gradient(180deg, var(--stage-top) 0%, #161616 55%, var(--stage-bottom) 100%);
    font-family: "Source Sans 3", "Myriad Pro", Arial, sans-serif;
    color: var(--ink);
  }
  .card {
    position: absolute;
    top: 306px;
    width: 440px;
    height: 271px;
    background: var(--card-amber);
    border-radius: 10px;
  }
  .card--front { left: 149px; }
  .card--back { left: 608px; }

  .wordmark {
    position: absolute;
    text-align: center;
    font-weight: 400;
    line-height: 1.05;
    color: var(--ink);
  }
  .wordmark span { display: block; }
  .card--front .wordmark {
    left: 14px;
    width: 196px;
    top: 101px;
    font-size: 27px;
  }
  .card--back .wordmark {
    left: 0;
    width: 440px;
    top: 78px;
    font-size: 50px;
  }

  .contact {
    position: absolute;
    left: 220px;
    top: 74px;
  }
  .contact__name {
    font-size: 16px;
    font-weight: 600;
    letter-spacing: 0.1px;
  }
  .contact__role {
    font-size: 12px;
    margin-top: 3px;
  }
  .contact__list {
    list-style: none;
    margin-top: 22px;
    font-size: 12.4px;
  }
  .contact__list li {
    display: flex;
    align-items: center;
    height: 18px;
  }
  .contact__icon {
    width: 9px;
    height: 9px;
    margin-right: 5px;
    fill: var(--ink);
    stroke: var(--ink);
  }
</style>
</head>
<body>
  <section class="card card--front" aria-label="Business card front">
    <h1 class="wordmark"><span>Mosaic</span><span>Interior Design</span></h1>
    <div class="contact">
      <p class="contact__name">Petra Wendlecombe</p>
      <p class="contact__role">Interior Designer &amp; Stylist</p>
      <ul class="contact__list">
        <li>
          <svg class="contact__icon" viewBox="0 0 10 10" aria-hidden="true">
            <path d="M1 3.2 Q5 0.5 9 3.2 L8.2 4.6 L6.6 3.9 L6.4 3 Q5 2.5 3.6 3 L3.4 3.9 L1.8 4.6 Z" stroke="none"/>
            <rect x="2" y="5" width="6" height="4" rx="0.6" stroke="none"/>
          </svg>
          +447311584209
        </li>
        <li>
          <svg class="contact__icon" viewBox="0 0 10 10" aria-hidden="true">
            <rect x="0.5" y="2" width="9" height="6.5" rx="0.5" stroke="none"/>
            <path d="M0.8 2.4 L5 5.8 L9.2 2.4" fill="none" stroke="var(--card-amber)" stroke-width="0.9"/>
          </svg>
          petra@mosaicinteriordesign.co.uk
        </li>
        <li>
          <svg class="contact__icon" viewBox="0 0 10 10" aria-hidden="true">
            <g fill="none" stroke-width="1.3" stroke-linecap="round">
              <path d="M4.2 5.8 L2.6 7.4 Q1.6 8.4 2.6 8.9 Q3.3 9.3 4 8.6 L5.4 7.2"/>
              <path d="M5.8 4.2 L7.4 2.6 Q8.4 1.6 7.9 1.1 Q7.2 0.6 6.4 1.4 L4.6 3.2"/>
              <path d="M3.8 6.2 L6.2 3.8"/>
            </g>
          </svg>
          wwww.mosaicinteriordesign.co.uk
        </li>
      </ul>
    </div>
  </section>

  <section class="card card--back" aria-label="Business card back">
    <h2 class="wordmark"><span>Mosaic</span><span>Interior Design</span></h2>
  </section>
</body>
</html>
```